Vegan bakery needs business card

We need a business card design for my vegan bakery in Philadelphia Pa. We create amazing whole food plant based cuisine that is egg and dairy free. We use fruits, vegetables, healing herbs, nuts, natural sugars (date, turbinado, agave) and non bleached flours in our creations. Due to demand and interest in the Philadelphia area we created a late night vegan dessert delivery service named Bramble Vegan. We are the only business providing delicious vegan desserts delivered to your door at 1am!! We would like to see designs that use the color scheme in the logo. The final design should communicate the benefits of our products: dairy/egg free, plant based, healing herbs, amazing food.

```html
<!DOCTYPE html>
<html lang="en">
<head>
<meta charset="utf-8">
<title>Wholly Crumb Desserts – Business Card</title>
<link rel="stylesheet" href="https://fonts.googleapis.com/css2?family=Questrial&display=swap">
<style>
  :root {
    --stage: #3b3b3d;
    --card: #1f1f20;
    --coral: #f07d5f;
    --green: #5cc43a;
    --white: #f2f2f2;
    --font: "Questrial", "Century Gothic", sans-serif;
  }
  * { box-sizing: border-box; margin: 0; padding: 0; }
  html, body {
    width: 1200px; height: 1189px; overflow: hidden;
    background: var(--stage);
    font-family: var(--font);
  }
  .card {
    position: absolute; left: 150px;
    width: 900px; height: 514px;
    background: var(--card);
    border-radius: 34px;
    overflow: hidden;
  }
  .card--front { top: 58px; }
  .card--back { top: 617px; }

  /* brand mark: plain name with one circle */
  .brand {
    display: flex; align-items: center; gap: 16px;
    color: var(--coral);
    font-size: 40px; line-height: 1;
    white-space: nowrap;
  }
  .brand__dot {
    width: 34px; height: 34px; border-radius: 50%;
    background: var(--coral); flex: none;
  }

  /* front */
  .front__inner {
    position: absolute; inset: 0;
    display: flex; flex-direction: column; align-items: center; justify-content: center;
    gap: 26px;
  }
  .front__heading { color: var(--green); font-size: 20px; letter-spacing: 1px; margin-top: 40px; }
  .front__benefits { color: var(--coral); font-size: 22px; margin-top: -14px; }

  /* back */
  .back__brand {
    position: absolute; left: 50px; top: 170px;
    display: flex; flex-direction: column; gap: 28px;
  }
  .back__brand .brand { font-size: 34px; gap: 14px; }
  .back__brand .brand__dot { width: 28px; height: 28px; }
  .slogan { color: var(--green); font-size: 34px; line-height: 1.1; padding-left: 44px; }

  .contact { position: absolute; left: 518px; top: 88px; width: 350px; }
  .contact__name { color: var(--coral); font-size: 30px; line-height: 1; }
  .contact__role { color: var(--white); font-size: 19px; margin-top: 4px; }
  .contact__rule { height: 2px; background: var(--green); margin: 10px 0 18px -6px; width: 350px; }
  .contact__list { list-style: none; display: flex; flex-direction: column; gap: 6px; }
  .contact__item { display: flex; align-items: center; gap: 10px; color: var(--white); font-size: 21px; white-space: nowrap; }
  .contact__item svg { width: 22px; height: 22px; flex: none; }
  .address { margin-top: 22px; color: var(--white); font-size: 21px; line-height: 1.3; white-space: nowrap; }
  .address__company { color: var(--coral); }

  .web-footer {
    position: absolute; left: 34px; right: 28px; bottom: 70px;
    display: flex; align-items: center; gap: 18px;
  }
  .web-rule { height: 2px; background: var(--green); }
  .web-rule--left { flex: 1; }
  .web-rule--right { width: 70px; flex: none; }
  .web { color: var(--green); font-size: 24px; line-height: 1; white-space: nowrap; flex: none; }
</style>
</head>
<body>

<section class="card card--front" aria-label="Card front">
  <div class="front__inner">
    <div class="brand"><span class="brand__dot"></span><span>Wholly Crumb Desserts</span></div>
    <p class="front__heading">OUR PRODUCTS</p>
    <p class="front__benefits">dairy/egg free, plant based, healing herbs, amazing food.</p>
  </div>
</section>

<section class="card card--back" aria-label="Card back">
  <div class="back__brand">
    <div class="brand"><span class="brand__dot"></span><span>Wholly Crumb Desserts</span></div>
    <p class="slogan">100% vegan<br>100% delicious</p>
  </div>

  <div class="contact">
    <p class="contact__name">Jonah Reyes</p>
    <p class="contact__role">Director of Marketing</p>
    <div class="contact__rule"></div>
    <ul class="contact__list">
      <li class="contact__item">
        <svg viewBox="0 0 24 24" aria-hidden="true"><circle cx="12" cy="12" r="11" fill="none" stroke="var(--coral)" stroke-width="2"/><rect x="8.5" y="6" width="7" height="12" rx="1.2" fill="none" stroke="var(--coral)" stroke-width="1.8"/></svg>
        215-555-0142
      </li>
      <li class="contact__item">
        <svg viewBox="0 0 24 24" aria-hidden="true"><circle cx="12" cy="12" r="11" fill="var(--coral)"/><path d="M6 10c0-2 3-3 6-3s6 1 6 3l-2 1-1-2h-6l-1 2zM8 12h8l1 5H7z" fill="var(--card)"/></svg>
        215-555-0143
      </li>
      <li class="contact__item">
        <svg viewBox="0 0 24 24" aria-hidden="true"><circle cx="12" cy="12" r="11" fill="var(--coral)"/><rect x="6" y="8" width="12" height="8" fill="var(--card)"/><path d="M6 8l6 5 6-5" fill="none" stroke="var(--coral)" stroke-width="1.4"/></svg>
        hello@whollycrumb.com
      </li>
    </ul>
    <p class="address">
      <span class="address__company">Wholly Crumb Desserts</span><br>
      Po Box 48, Orchard Lane<br>
      Media, PA 19063
    </p>
  </div>

  <div class="web-footer">
    <div class="web-rule web-rule--left"></div>
    <p class="web">www.whollycrumb.com</p>
    <div class="web-rule web-rule--right"></div>
  </div>
</section>

</body>
</html>
```